Need Web Design for Business Process Outsourcing Company (Quorvane)

Quorvane is a business process outsourcing company. Need a simple site similar to http://www.tallowbrinkhire.com/ but with a more professional and credible look. New to the process; not sure where to start and comparing my options. Please let me know what my options are if I choose to go with you. Logo is attached for your reference. Please use same colorway

Reason: I want the final product to be coded. Please confirm you will be able to code final design.

Industry/Entity Type

Business

Coding

Coded - Design and coding required

```html
<!DOCTYPE html>
<html lang="en">
<head>
<meta charset="utf-8">
<title>Quorvane — Business Process Outsourcing</title>
<link href="https://fonts.googleapis.com/css2?family=Raleway:ital,wght@0,400;0,500;0,600;0,700;1,400&display=swap" rel="stylesheet">
<style>
:root{
  --blue:#0a8fd0;
  --navy:#0b5a96;
  --orange:#d97a0f;
  --ink:#222;
  --muted:#666;
  --band:#f4f4f4;
  --footer:#1a1a1a;
  --white:#fff;
}
*{margin:0;padding:0;box-sizing:border-box}
html,body{width:794px;height:1200px;overflow:hidden;background:var(--white)}
body{position:relative;font-family:"Raleway",sans-serif;color:var(--ink)}
.abs{position:absolute}
/* hero */
.hero{left:0;top:0;width:794px;height:325px;border-radius:0 0 70px 70px/0 0 60px 60px;
  background:linear-gradient(100deg,#8a9197 0%,#9ca3a9 45%,#6f7a86 70%,#1d2430 100%);overflow:hidden}
.hero-visual{right:0;top:0;width:360px;height:325px;
  background:linear-gradient(90deg,rgba(120,140,160,0) 0%,rgba(70,120,170,.35) 40%,#1c222c 90%)}
.nav{left:162px;top:7px;width:471px;height:33px;background:var(--white);display:flex;align-items:center;padding:0 6px}
.brand{display:flex;align-items:center;gap:4px;font-weight:700;font-size:14px;color:var(--navy)}
.brand-mark{width:18px;height:18px;background:var(--navy)}
.menu{display:flex;gap:14px;margin-left:auto;margin-right:12px;font-size:5.5px;font-weight:500;color:#333;list-style:none;height:33px;align-items:center}
.menu li{height:33px;display:flex;align-items:center}
.menu .active{color:var(--blue);border-bottom:2px solid var(--navy)}
.search{width:14px;height:14px;border-radius:50%;background:var(--blue);display:flex;align-items:center;justify-content:center}
.slide-dots{left:753px;top:161px;display:flex;flex-direction:column;gap:3px}
.slide-dots span{width:4px;height:4px;border-radius:50%;background:var(--white)}
.slide-dots .on{background:var(--blue)}
.hero-title{left:155px;top:207px;font-size:8px;font-weight:700;color:var(--white)}
.hero-text{left:155px;top:228px;width:280px;font-size:8.4px;line-height:12px;color:var(--white)}
.btn{display:flex;align-items:center;justify-content:center;border-radius:12px;background:var(--orange);color:var(--white);font-weight:700}
.hero-btn{left:155px;top:261px;width:71px;height:19px;font-size:4.8px}
/* headings */
.kicker{width:12px;height:2px;background:var(--blue)}
.h2{font-size:10px;font-weight:700;color:var(--ink)}
.lead{font-size:6px;line-height:10px;font-weight:500}
.small{font-size:4.8px;line-height:8.2px;color:var(--muted)}
.more{font-size:4.8px;font-weight:700;color:var(--navy)}
/* about */
.about-photo{left:404px;top:357px;width:235px;height:132px;border:2px solid #e3e3e3;
  background:linear-gradient(90deg,#d9dde2,#8e8a86 40%,#2e4b8a 60%,#e8e6e3 80%,#f6f4f2)}
/* services */
.services{left:0;top:506px;width:794px;height:274px;background:var(--band)}
.card{top:582px;width:109px;height:166px;background:var(--white);box-shadow:0 1px 2px rgba(0,0,0,.08)}
.card-top{height:89px;display:flex;align-items:center;justify-content:center;position:relative}
.card-tag{position:absolute;right:0;bottom:0;height:9px;width:53px;display:flex;font-size:3.8px;font-weight:700;color:var(--white)}
.card-tag b{flex:1;display:flex;align-items:center;justify-content:center}
.card-tag i{width:8px;background:var(--navy);display:flex;align-items:center;justify-content:center;font-style:normal}
.card-body{padding:13px 12px}
.card-body h3{font-size:7px;font-weight:700;margin:3px 0 7px}
.arrow{top:652px}
/* news */
.post{top:836px;width:128px}
.post-date{font-size:4.4px;color:#888}
.post-title{font-size:7.4px;font-weight:500;line-height:10.4px;margin-top:2px}
.testimonial{left:483px;top:834px;width:150px;height:108px;background:#f7f7f7;text-align:center;padding:18px 18px}
.testimonial p{font-size:4.9px;line-height:9px;font-style:italic;color:#888}
.nav-sq{width:16px;height:16px;display:flex;align-items:center;justify-content:center}
/* cta */
.cta{left:0;top:976px;width:794px;height:58px;background:var(--blue);border-radius:70px 70px 0 0/44px 44px 0 0}
.cta-text{left:192px;top:996px;font-size:15px;color:var(--white)}
.cta-btn{left:521px;top:993px;width:90px;height:24px;font-size:6.4px}
/* footer */
.footer{left:0;top:1032px;width:794px;height:168px;background:var(--footer);color:#ccc}
.f-head{font-size:6px;font-weight:700;color:var(--white);top:1060px}
.f-list{list-style:none;font-size:4.9px;line-height:10.4px;color:#bbb;top:1075px}
.f-list li::before{content:"› ";color:#ddd}
.subscribe{left:155px;top:1117px;width:108px;height:17px;border:1px solid #444;display:flex}
.subscribe span{flex:1;font-size:4.8px;font-style:italic;color:#999;padding:5px 7px}
.subscribe i{width:16px;background:var(--blue)}
.f-rule{left:155px;top:1175px;width:483px;height:1px;background:#333}
.social{top:1180px;width:12px;height:12px;border:1px solid #444}
</style>
</head>
<body>

<section class="hero abs">
  <div class="hero-visual abs" role="img" aria-label="Businessman's hand holding a glowing globe with network lines"></div>
</section>

<header class="nav abs">
  <div class="brand"><span class="brand-mark"></span>Quorvane</div>
  <ul class="menu">
    <li class="active">HOME</li><li>SERVICES</li><li>PORTFOLIO</li><li>ABOUT US</li><li>NEWS</li><li>CONTACT</li>
  </ul>
  <div class="search"><svg width="7" height="7" viewBox="0 0 10 10"><circle cx="4" cy="4" r="3" fill="none" stroke="#fff" stroke-width="1.4"/><line x1="6.2" y1="6.2" x2="9" y2="9" stroke="#fff" stroke-width="1.4"/></svg></div>
</header>

<div class="slide-dots abs"><span class="on"></span><span></span><span></span><span></span></div>

<h1 class="hero-title abs">WE ARE A BPO BUSINESS PROCESS OUTSOURCING COMPANY</h1>
<p class="hero-text abs">Nullam faucibus augue non pretium dignissim. Sed ornare sodales nunc a fermentum.</p>
<div class="hero-btn btn abs">VIEW DETAILS</div>

<div class="kicker abs" style="left:161px;top:373px"></div>
<h2 class="h2 abs" style="left:161px;top:377px">ABOUT US</h2>
<p class="lead abs" style="left:161px;top:395px;width:230px">Lorem ipsum dolor sit amet, consectetur adipiscing elit. Nunc sollicitudin, nibh sed aliquam fermentum</p>
<p class="small abs" style="left:161px;top:424px;width:230px">Nullam faucibus augue non pretium dignissim. Sed ornare sodales nunc a fermentum. Pellentesque habitant morbi tristique senectus et netus et malesuada fames ac turpis egestas. Maecenas tincidunt orci in libero euismod commodo. Suspendisse feugiat, nibh a rutrum ullamcorper.</p>
<p class="more abs" style="left:161px;top:463px">READ MORE ›</p>
<div class="about-photo abs" role="img" aria-label="Row of call centre agents wearing headsets"></div>

<section class="services abs"></section>
<h2 class="h2 abs" style="left:0;width:794px;text-align:center;top:536px">OUR SERVICES</h2>
<p class="small abs" style="left:0;width:794px;text-align:center;top:548px">Donec ornare pellentesque tellus sed porttitor</p>
<div class="kicker abs" style="left:391px;top:560px"></div>

<svg class="arrow abs" style="left:123px" width="16" height="28" viewBox="0 0 16 28"><polyline points="14,1 2,14 14,27" fill="none" stroke="#bbb" stroke-width="1"/></svg>
<svg class="arrow abs" style="left:656px" width="16" height="28" viewBox="0 0 16 28"><polyline points="2,1 14,14 2,27" fill="none" stroke="#bbb" stroke-width="1"/></svg>

<article class="card abs" style="left:161px">
  <div class="card-top" style="background:var(--blue)">
    <svg width="28" height="28" viewBox="0 0 28 28"><circle cx="12" cy="15" r="7" fill="none" stroke="#fff" stroke-width="4" stroke-dasharray="3 2.5"/><circle cx="12" cy="15" r="2.5" fill="#fff"/><circle cx="21" cy="7" r="4" fill="none" stroke="#fff" stroke-width="2.5" stroke-dasharray="2 1.6"/></svg>
    <div class="card-tag"><b style="background:#2aa2dc">READ MORE</b><i>›</i></div>
  </div>
  <div class="card-body"><div class="kicker"></div><h3>CUSTOMER SERVICE</h3><p class="small">Lorem ipsum dolor sit amet, consectetur adipiscing elit. Mauris faucibus sapien ut elit condimentum congue.</p></div>
</article>
<article class="card abs" style="left:282px">
  <div class="card-top" style="background:var(--navy)">
    <svg width="26" height="24" viewBox="0 0 26 24"><path d="M1 3h4l3 12h13l3-9H7" fill="none" stroke="#fff" stroke-width="2.6"/><circle cx="10" cy="20" r="2.2" fill="#fff"/><circle cx="19" cy="20" r="2.2" fill="#fff"/></svg>
    <div class="card-tag"><b style="background:var(--orange)">READ MORE</b><i style="background:#a85a05">›</i></div>
  </div>
  <div class="card-body"><div class="kicker"></div><h3>ECOMMERCE</h3><p class="small">Lorem ipsum dolor sit amet, consectetur adipiscing elit. Mauris faucibus sapien ut elit condimentum congue.</p></div>
</article>
<article class="card abs" style="left:403px">
  <div class="card-top" style="background:var(--navy)">
    <svg width="26" height="26" viewBox="0 0 26 26"><path d="M24 2 12 16l-2-2Z" fill="#fff"/><path d="M9 15c-4 0-6 3-6 8 4 0 9-1 9-5Z" fill="#fff"/></svg>
    <div class="card-tag"><b style="background:#2aa2dc">READ MORE</b><i>›</i></div>
  </div>
  <div class="card-body"><div class="kicker"></div><h3>CREATIVE</h3><p class="small">Lorem ipsum dolor sit amet, consectetur adipiscing elit. Mauris faucibus sapien ut elit condimentum congue.</p></div>
</article>
<article class="card abs" style="left:524px">
  <div class="card-top" style="background:var(--navy)">
    <svg width="28" height="24" viewBox="0 0 28 24"><rect x="1" y="6" width="26" height="17" rx="3" fill="#fff"/><rect x="9" y="1.5" width="10" height="6" rx="1.5" fill="none" stroke="#fff" stroke-width="2"/><rect x="7" y="6" width="1.6" height="17" fill="var(--navy)"/><rect x="19.4" y="6" width="1.6" height="17" fill="var(--navy)"/></svg>
    <div class="card-tag"><b style="background:#2aa2dc">READ MORE</b><i>›</i></div>
  </div>
  <div class="card-body"><div class="kicker"></div><h3>IT SOLUTIONS</h3><p class="small">Lorem ipsum dolor sit amet, consectetur adipiscing elit. Mauris faucibus sapien ut elit condimentum congue.</p></div>
</article>

<div class="kicker abs" style="left:161px;top:810px;background:#9cc63b"></div>
<h2 class="h2 abs" style="left:161px;top:813px">LATEST NEWS</h2>

<svg class="abs" style="left:161px;top:835px" width="14" height="14" viewBox="0 0 14 14"><rect x="1" y="2" width="12" height="11" fill="none" stroke="#0b5a96" stroke-width="1.4"/><rect x="1" y="2" width="12" height="3" fill="#0b5a96"/><path d="M3 7h2M6 7h2M9 7h2M3 9.5h2M6 9.5h2M9 9.5h2" stroke="#0b5a96"/></svg>
<div class="post abs" style="left:184px">
  <p class="post-date">APRIL 22, 2016</p>
  <p class="post-title">Vestibulum ante ipsum primis in faucibus orci luctus</p>
  <p class="small" style="margin-top:8px">Donec ornare pellentesque tellus sed porttitor. Sed porta nec leo et scelerisque. Nullam at est interdum, hendrerit nibh in, efficitur neque. Proin lobortis metus vel nisl faucibus, id eleifend lorem laoreet.</p>
  <p class="more" style="text-align:right;margin-top:6px">READ MORE ›</p>
</div>
<svg class="abs" style="left:322px;top:835px" width="14" height="14" viewBox="0 0 14 14"><rect x="1" y="2" width="12" height="11" fill="none" stroke="#0b5a96" stroke-width="1.4"/><rect x="1" y="2" width="12" height="3" fill="#0b5a96"/><path d="M3 7h2M6 7h2M9 7h2M3 9.5h2M6 9.5h2M9 9.5h2" stroke="#0b5a96"/></svg>
<div class="post abs" style="left:345px">
  <p class="post-date">APRIL 22, 2016</p>
  <p class="post-title">Vestibulum ante ipsum primis in faucibus orci luctus</p>
  <p class="small" style="margin-top:8px">Tellus sed porttitor. Sed porta nec leo et scelerisque. Nullam at est interdum, hendrerit nibh in, efficitur neque. Proin lobortis metus vel nisl faucibus, id eleifend lorem laoreet. Maecenas sit amet lorem eu purus rutrum interdum.</p>
  <p class="more" style="text-align:right;margin-top:6px">READ MORE ›</p>
</div>

<div class="kicker abs" style="left:484px;top:810px;background:#9cc63b"></div>
<h2 class="h2 abs" style="left:484px;top:813px">WHAT CLIENTS SAY</h2>
<div class="testimonial abs">
  <p>Nam et libero nec ex tincidunt malesuada vel sit amet arcu. Sed sit amet est nec quam hendrerit hendrerit. Curabitur ut pulvinar mi.</p>
  <p style="font-style:normal;font-weight:700;color:#333;margin-top:20px">MAREN TOLLIVER</p>
  <p style="font-style:normal;font-weight:600;margin-top:0">TLOREM ISPUM DOLOR SIT</p>
</div>
<div class="nav-sq abs" style="left:484px;top:881px;background:#1e2a36"><svg width="5" height="7" viewBox="0 0 5 7"><polyline points="4,1 1,3.5 4,6" fill="none" stroke="#fff" stroke-width="1.3"/></svg></div>
<div class="nav-sq abs" style="left:617px;top:881px;background:var(--blue)"><svg width="5" height="7" viewBox="0 0 5 7"><polyline points="1,1 4,3.5 1,6" fill="none" stroke="#fff" stroke-width="1.3"/></svg></div>

<section class="cta abs"></section>
<p class="cta-text abs">Lorem ipsum dolor sit amet, consectetur adi</p>
<div class="cta-btn btn abs">QUICK CONTACT</div>

<footer class="footer abs"></footer>
<h4 class="f-head abs" style="left:155px">NEWSLETTER SUBSCRIBE</h4>
<p class="abs" style="left:155px;top:1077px;width:110px;font-size:4.9px;line-height:8.4px;color:#bbb">Subscribe to our newsletter and we will inform you about newset projects and promotions.</p>
<div class="subscribe abs"><span>Your email address</span><i></i></div>

<h4 class="f-head abs" style="left:324px">QUICK LINKS</h4>
<ul class="f-list abs" style="left:324px"><li>Home</li><li>About</li><li>Services</li><li>Gallery</li><li>Testimonials</li><li>Portfolio</li><li>Contact</li></ul>

<h4 class="f-head abs" style="left:437px">MORE LINKS</h4>
<ul class="f-list abs" style="left:437px"><li>Privacy Policy</li><li>Terms &amp; Conditions</li><li>FAQ</li><li>Lorem</li><li>Ipsum dolor</li><li>Dolor sit amit</li><li>More</li></ul>

<h4 class="f-head abs" style="left:558px">CONTACT US</h4>
<address class="abs" style="left:558px;top:1076px;font-style:normal;font-size:4.9px;line-height:8.6px;color:#bbb">
  18 Harlow Crescent, Brindle Cove, NL<br>B2K 7R1
  <span style="display:block;font-size:7px;color:#fff;margin:5px 0 4px">Phone: 555.214.3380</span>
  Fax: 555.214.3391<br>hello@quorvane.com
</address>

<div class="f-rule abs"></div>
<p class="abs" style="left:155px;top:1185px;font-size:4.4px;color:#bbb">COPYRIGHT 2016 © QUORVANE. ALL RIGHTS RESERVED</p>
<div class="social abs" style="left:599px"></div>
<div class="social abs" style="left:613px"></div>
<div class="social abs" style="left:627px"></div>

</body>
</html>
```